Business Card for Vorla Parts Wholesale supplier

Hi There! I need a new business card for our company. We are specialized in selling Vorla parts, mostly we sell new LCD screens for Zelnar and Drelks. I would like to see that back in the design.

You can find the colors and logo's on our website: www.hartuvo.nl

Industry/Entity Type

Business

Contact Information for Business Card

My Details:
Tobias Lindqvist

Phone: 0031687203316
E-mail: Tobias@hartuvo.nl

Slogan: "Because Quality Matters"

Font styles to use
Sans Serif

Colors

Designer to choose colors to be used in the design.

Requirements
Must have
• A Black backside with the Hartuvo logo on it. The front side should be clean with only my contact details.
• But I'm also open for something really different or awesome!
Nice to have
• Remember that we are in the parts & repairing industry, So i'll be handing those business cards mainly to repair companies. Maybe you can do something with that thought :)

```html
<!DOCTYPE html>
<html lang="en">
<head>
<meta charset="utf-8">
<title>Hartuvo Business Card</title>
<link rel="stylesheet" href="https://fonts.googleapis.com/css2?family=Open+Sans:wght@400;600&family=Work+Sans:wght@400;500;600&display=swap">
<style>
  :root {
    --stage: #c9c9c9;
    --card-white: #ffffff;
    --card-black: #1b1b1b;
    --accent: #f26f21;
    --ink-grey: #6b6b6b;
    --ink-white: #ffffff;
  }
  * { margin: 0; padding: 0; box-sizing: border-box; }
  html, body {
    width: 1200px; height: 1000px; overflow: hidden;
    background: var(--stage);
  }
  .sheet {
    width: 1200px; height: 1000px;
    display: flex; align-items: center; justify-content: center; gap: 40px;
  }
  .card {
    width: 540px; height: 336px; position: relative;
    box-shadow: 0 4px 14px rgba(0,0,0,0.25);
  }
  .card--front { background: var(--card-white); font-family: "Open Sans", sans-serif; }
  .card--back { background: var(--card-black); font-family: "Work Sans", sans-serif; }

  .holder-name {
    position: absolute; left: 30px; top: 158px;
    font-size: 21px; font-weight: 600; letter-spacing: 0.5px;
    color: var(--ink-grey);
  }
  .holder-name .surname { color: var(--accent); }

  .contact-list {
    position: absolute; left: 30px; top: 218px;
    list-style: none;
  }
  .contact-list li {
    display: flex; align-items: center; gap: 12px;
    font-size: 13px; color: var(--ink-grey); height: 22px;
  }
  .contact-list svg { width: 12px; height: 12px; fill: var(--accent); flex: none; }
  .contact-list .domain { color: var(--accent); }

  .brand {
    position: absolute; left: 0; right: 0; top: 118px;
    display: flex; align-items: center; justify-content: center; gap: 14px;
  }
  .brand-dot {
    width: 40px; height: 40px; border-radius: 50%; background: var(--accent);
  }
  .brand-name {
    font-size: 50px; font-weight: 600; color: var(--ink-white);
    letter-spacing: 1px; line-height: 1;
  }
  .slogan {
    position: absolute; left: 0; right: 0; top: 246px; text-align: center;
    font-size: 14px; color: var(--ink-white); letter-spacing: 1px;
  }
  .slogan .highlight { color: var(--accent); }
</style>
</head>
<body>
<main class="sheet">
  <section class="card card--front" aria-label="Card front">
    <p class="holder-name">TOBIAS <span class="surname">LINDQVIST</span></p>
    <ul class="contact-list">
      <li>
        <svg viewBox="0 0 24 24" aria-hidden="true"><path d="M6.6 10.8a15.1 15.1 0 0 0 6.6 6.6l2.2-2.2a1 1 0 0 1 1-.25 11.4 11.4 0 0 0 3.6.57 1 1 0 0 1 1 1V20a1 1 0 0 1-1 1A17 17 0 0 1 3 4a1 1 0 0 1 1-1h3.5a1 1 0 0 1 1 1c0 1.25.2 2.45.57 3.57a1 1 0 0 1-.25 1z"/></svg>
        0031687203316
      </li>
      <li>
        <svg viewBox="0 0 24 24" aria-hidden="true"><path d="M2 5h20v14H2z M3 6l9 7 9-7" fill="none" stroke="#f26f21" stroke-width="2"/><path d="M2 5h20l-10 8z"/></svg>
        Tobias@hartuvo.nl
      </li>
      <li>
        <svg viewBox="0 0 24 24" aria-hidden="true"><circle cx="12" cy="12" r="10"/><path d="M2 12h20M12 2c3 3 3 17 0 20M12 2c-3 3-3 17 0 20" fill="none" stroke="#fff" stroke-width="1.4"/></svg>
        <span>www.<span class="domain">hartuvo</span>.nl</span>
      </li>
    </ul>
  </section>

  <section class="card card--back" aria-label="Card back">
    <div class="brand">
      <span class="brand-dot" aria-hidden="true"></span>
      <span class="brand-name">hartuvo</span>
    </div>
    <p class="slogan">Because <span class="highlight">Quality</span> Matters</p>
  </section>
</main>
</body>
</html>
```